2022 Yearly Patron Drive (art gallery annual report)

6X9, 16-page brochure that serves both as an annual report for the previous year and gets mailed for an ask for donations. This must be done in InDesign and I will provide a template. I am also sending PDFs for the previous two years. Last year was pink and black, but I have recolored the logo purple this year.. so am open to whatever colors. I used last year's template to put in the new info. The theme for this year is Amazing - last year was Thriving. The font I chose for the front I do not want to use.. its just an example. All three pictures on the front don't have to be used.. just ideas.
Updates

I put three photos on the front page. It isn't necessary to use all of them, I thought there might be something there to use as part of the design

The current information is in the InDesign file, Calatalog Design.indd with the to Links Folders attached.

Target Market(s)

Donors

Industry/Entity Type

Art

Font styles to use
Sans Serif

Requirements
Must have
• InDesign
Nice to have
• A new look! Something different than 2021 an 2020 (PDFs included)

```html
<!DOCTYPE html>
<html lang="en">
<head>
<meta charset="utf-8">
<title>Activities – Yearly Patron Drive</title>
<link href="https://fonts.googleapis.com/css2?family=Bebas+Neue&family=Montserrat:wght@300;700&display=swap" rel="stylesheet">
<style>
  :root {
    --purple: #8f449c;
    --ink: #231f20;
    --body-text: #5b5b5b;
    --paper: #ffffff;
  }
  html, body {
    margin: 0;
    padding: 0;
    overflow: hidden;
    background: var(--paper);
  }
  .page {
    position: relative;
    width: 1200px;
    height: 800px;
    overflow: hidden;
    background: var(--paper);
  }
  .section-band {
    position: absolute;
    left: 0;
    top: 71px;
    width: 362px;
    height: 87px;
    background: var(--purple);
  }
  .section-band-accent {
    position: absolute;
    left: 369px;
    top: 71px;
    width: 8px;
    height: 87px;
    background: var(--purple);
  }
  .section-title {
    position: absolute;
    left: 110px;
    top: 80px;
    margin: 0;
    font-family: "Bebas Neue", sans-serif;
    font-weight: 400;
    font-size: 70px;
    line-height: 70px;
    color: var(--paper);
    letter-spacing: 0.005em;
  }
  .brand-name {
    position: absolute;
    right: 48px;
    top: 74px;
    margin: 0;
    font-family: "Montserrat", sans-serif;
    font-weight: 700;
    font-size: 76px;
    line-height: 76px;
    letter-spacing: 0.08em;
    color: var(--ink);
  }
  .story {
    position: absolute;
    left: 105px;
    top: 241px;
    width: 986px;
    height: 336px;
    border-left: 5px solid var(--purple);
    box-sizing: border-box;
    padding-left: 34px;
    padding-top: 12px;
  }
  .story p {
    margin: 0 0 14.5px;
    font-family: "Montserrat", sans-serif;
    font-weight: 300;
    font-size: 17.2px;
    line-height: 22.3px;
    color: var(--body-text);
    text-align: justify;
    text-align-last: left;
  }
  .folio-band {
    position: absolute;
    left: 0;
    top: 740px;
    width: 61px;
    height: 20px;
    background: var(--purple);
  }
  .folio-number {
    position: absolute;
    left: 44px;
    top: 740px;
    font-family: "Montserrat", sans-serif;
    font-weight: 700;
    font-size: 12px;
    line-height: 20px;
    color: var(--paper);
  }
  .folio-accent {
    position: absolute;
    left: 65px;
    top: 740px;
    width: 3px;
    height: 20px;
    background: var(--purple);
  }
  .theme-word {
    position: absolute;
    left: 78px;
    top: 726px;
    margin: 0;
    font-family: "Bebas Neue", sans-serif;
    font-weight: 400;
    font-size: 51px;
    line-height: 51px;
    color: var(--purple);
  }
</style>
</head>
<body>
<main class="page">
  <div class="section-band"></div>
  <div class="section-band-accent"></div>
  <h1 class="section-title">Activities</h1>

  <p class="brand-name">MARLOW</p>

  <section class="story">
    <p>In 2021, we hosted several notable events. The first was welcoming Santa to our decked-out halls. Our pint-sized Marlow Guild supporters enjoyed miniature stockings filled with candy as they waited to tell Santa what they hoped he would bring them for Christmas.</p>
    <p>The second event was even more special. Ruth Delaney, who was dear to many members’ hearts, passed away, but through the generosity of her husband, Tom Delaney and her family, we were able to host a sale of many of her treasures featuring her impeccable taste. Her creations keep appearing all over town reminding us of her love of collecting and creating.</p>
    <p>Several of our events involve our new neighbors--Cedar Ridge Vintners, who have been a partner for the recent open houses at the Marlow Gallery. Guests were able to enjoy delicious wines created by Cedar Ridge College students. The Vintners tasting room is also open on Fridays and Saturdays of each month, between 12-5:00 and on the last Friday of the month offers extended hours until 7 pm. Wine, art, and cheese plates--all under one roof. What a great way to end your work weeks and join us.</p>
  </section>

  <div class="folio-band"></div>
  <span class="folio-number">8</span>
  <div class="folio-accent"></div>
  <p class="theme-word">AMAZING</p>
</main>
</body>
</html>
```